Business cards for KORU Real Estate Holdings LLC

We need a cool, original business card design for a company based in the Washington DC metropolitan area. We are a new energetic and passionate Real Estate Investing Company that invests in all types of real estate; commercial, residential, industrial etc.

Our company color is Red since it reflects action, energy and speed; it is assertive confident, energizing, exciting, powerful, passionate and determined. So we would like business card communicate those qualities to the audience.

Our audiences are investors that want to invest with us, real estate sellers, buyers, and tenants who lease from us.

Our logo is attached

```html
<!DOCTYPE html>
<html lang="en">
<head>
<meta charset="utf-8">
<title>KORU Real Estate Holdings LLC – Business Card</title>
<link rel="stylesheet" href="https://fonts.googleapis.com/css2?family=Open+Sans:wght@400;700&display=swap">
<style>
  :root {
    --card-bg: #e8eae9;
    --charcoal: #3b3b3d;
    --text-dark: #3a3a3a;
    --text-mid: #555558;
    --brand-red: #e0282e;
    --icon-fg: #ffffff;
  }
  html, body {
    margin: 0;
    padding: 0;
    width: 1200px;
    height: 777px;
    overflow: hidden;
    background: var(--card-bg);
    font-family: "Open Sans", Arial, sans-serif;
  }
  .card {
    position: relative;
    width: 1200px;
    height: 777px;
    background: var(--card-bg);
    overflow: hidden;
  }
  .card__edge {
    position: absolute;
    left: 0;
    top: 0;
    width: 220px;
    height: 777px;
  }
  .brand {
    position: absolute;
    left: 320px;
    top: 176px;
    display: flex;
    align-items: center;
    gap: 30px;
  }
  .brand__dot {
    width: 100px;
    height: 100px;
    border-radius: 50%;
    background: var(--brand-red);
  }
  .brand__name {
    font-weight: 700;
    font-size: 124px;
    letter-spacing: 6px;
    line-height: 1;
    color: var(--text-dark);
  }
  .contact {
    position: absolute;
    left: 300px;
    top: 500px;
    margin: 0;
    font-style: normal;
    color: var(--text-dark);
  }
  .contact__address {
    font-size: 28px;
    line-height: 42px;
    margin: 0 0 4px;
  }
  .contact__list {
    list-style: none;
    margin: 0;
    padding: 0;
  }
  .contact__item {
    display: flex;
    align-items: center;
    gap: 16px;
    font-size: 24px;
    line-height: 42px;
    color: var(--text-mid);
  }
  .contact__icon {
    width: 24px;
    height: 24px;
    flex: none;
  }
  .person {
    position: absolute;
    right: 44px;
    top: 624px;
    text-align: right;
    color: var(--text-dark);
  }
  .person__name {
    margin: 0;
    font-size: 38px;
    line-height: 48px;
    font-weight: 400;
  }
  .person__name strong { font-weight: 700; }
  .person__title {
    margin: 2px 0 0;
    font-size: 25px;
    color: var(--text-mid);
  }
</style>
</head>
<body>
<main class="card">
  <svg class="card__edge" viewBox="0 0 220 777" aria-hidden="true">
    <path d="M0 0 H110 C40 180 20 420 60 777 H0 Z" fill="var(--charcoal)"/>
    <path d="M132 0 C60 200 40 460 78 777" fill="none" stroke="var(--brand-red)" stroke-width="12"/>
  </svg>

  <div class="brand">
    <span class="brand__dot" aria-hidden="true"></span>
    <span class="brand__name">KORU</span>
  </div>

  <address class="contact">
    <p class="contact__address">Riverside Avenue 1820<br>Arlington VA # 2209</p>
    <ul class="contact__list">
      <li class="contact__item">
        <svg class="contact__icon" viewBox="0 0 24 24" aria-hidden="true"><circle cx="12" cy="12" r="12" fill="var(--charcoal)"/><path d="M8 6 L10.5 6 L11.2 9 L9.8 10.2 C10.5 11.8 12 13.4 13.8 14.2 L15 12.8 L18 13.5 L18 16 C12 17 7 12 8 6 Z" fill="var(--icon-fg)"/></svg>
        123-456-7890
      </li>
      <li class="contact__item">
        <svg class="contact__icon" viewBox="0 0 24 24" aria-hidden="true"><circle cx="12" cy="12" r="12" fill="var(--charcoal)"/><rect x="8.5" y="5" width="7" height="14" rx="1.5" fill="var(--icon-fg)"/><rect x="9.8" y="7" width="4.4" height="8" fill="var(--charcoal)"/></svg>
        123-456-7890
      </li>
      <li class="contact__item">
        <svg class="contact__icon" viewBox="0 0 24 24" aria-hidden="true"><circle cx="12" cy="12" r="12" fill="var(--charcoal)"/><rect x="6" y="10" width="12" height="7" rx="1" fill="var(--icon-fg)"/><rect x="8.5" y="6" width="7" height="4" fill="var(--icon-fg)"/></svg>
        123-456-7890
      </li>
      <li class="contact__item">
        <svg class="contact__icon" viewBox="0 0 24 24" aria-hidden="true"><rect x="3" y="6" width="18" height="12" rx="1" fill="var(--charcoal)"/><path d="M3.5 6.8 L12 13 L20.5 6.8" fill="none" stroke="var(--icon-fg)" stroke-width="1.5"/></svg>
        hello@koruholdings.com
      </li>
    </ul>
  </address>

  <div class="person">
    <p class="person__name"><strong>Daniel</strong> Harper</p>
    <p class="person__title">Owner / C.E.O.</p>
  </div>
</main>
</body>
</html>
```